Etiketten-Design für Dankeswein
Zielgruppe
Kelvora:
Wir stellen für unsere Kunden einen Dankeswein her. Er soll eine Hommage an die Freundschaft und Partnerschaft sein.
Subtitle, could be, but perhaps not:
When we gather, good things unfold.
Name: Kelvora (evtl. Änderung auf Tarnis)
Aufgabenstellung
Das Ettikett darf auch bunt sein, aber es sollte vorallem sehr Professionell sein.
Der Wein wird rötlich sein, die Flasche weiss durchsichtig. Es werden wahrscheinlich 0,5l Flaschen.
Die Form des Ettikets, kann noch definiert werden.
Es geht um eine Homage an das Treffen von Menschen und die Freundschaft.
Kelvora
Hintergrundinfos, die eher für den Hintergrund, Einarbeitung und kleine Abbildung gedacht sind.
PLORAX: ist eine IT Firma, die von 2 Partnern gegründet wurde. Das Logo sollte mit drauf, evtl. kann man auch sich an diesen Farben orientieren.
Familie Dormak: Die Tiersymbole repräsentieren die beiden Eltern. Das geschwungene H ist das Familienzeichen. Wenn man es rotiert. ähnelt es wieder einem Schmetterling. Vielleicht kann man da grafisch etwas machen?
Das geschwungene H oder die Tiersymbole haben hohen emotionalen Wert. In dem Wappen ist das neue Familiensymbol eingearbeitet in das noch ältere Familienwappen der Familie. Prio hat das geschwungene H
Für das Ettikett gibt es leider rechtliche Pflichtangaben:
PLORAX GmbH
Lindauring 14 CH-4057 Basel
Erzeugerab füllung:D- RP 7 348 962
A.P.-Nr.7 348 962 XXXX
11,0%vol 50 cl Enthält Sulfite
Deutscher Qualitätswein – Mosel
kelvora-beispiel.eu

```html
<!DOCTYPE html>
<html lang="de">
<head>
<meta charset="utf-8">
<title>Kelvora – Rotling 2020 Etikett</title>
<link href="https://fonts.googleapis.com/css2?family=Aldrich&display=swap" rel="stylesheet">
<style>
  :root {
    --page: #ffffff;
    --label-black: #000000;
    --band-white: #ffffff;
    --gold: #c2a955;
    --gold-soft: #cdb566;
    --wine-red: #a3142a;
    --band-edge: #e6e6e6;
  }
  html, body {
    margin: 0;
    padding: 0;
    width: 848px;
    height: 1200px;
    overflow: hidden;
    background: var(--page);
  }
  .canvas {
    position: relative;
    width: 848px;
    height: 1200px;
    background: var(--page);
  }
  .label {
    position: absolute;
    left: 64px;
    top: 252px;
    width: 720px;
    height: 696px;
    display: flex;
    flex-direction: column;
    font-family: "Aldrich", sans-serif;
  }
  .label__head {
    height: 453px;
    background: var(--label-black);
    position: relative;
  }
  .brand-name {
    position: absolute;
    left: 0;
    right: 0;
    top: 130px;
    margin: 0;
    text-align: center;
    font-family: "Aldrich", sans-serif;
    font-weight: 400;
    font-size: 104px;
    line-height: 1;
    letter-spacing: 1px;
    color: var(--gold);
  }
  .tagline {
    position: absolute;
    left: 0;
    right: 0;
    top: 352px;
    margin: 0;
    text-align: center;
    font-size: 24px;
    line-height: 37px;
    letter-spacing: 1.5px;
    color: var(--gold-soft);
  }
  .label__variety {
    height: 116px;
    background: var(--band-white);
    border-left: 1px solid var(--band-edge);
    border-right: 1px solid var(--band-edge);
    box-sizing: border-box;
    display: flex;
    flex-direction: column;
    align-items: center;
    justify-content: center;
    color: var(--wine-red);
    font-size: 28px;
    line-height: 37px;
    letter-spacing: 2px;
  }
  .label__foot {
    height: 127px;
    background: var(--label-black);
    display: flex;
    align-items: center;
    justify-content: center;
  }
  .family-name {
    font-family: "Aldrich", sans-serif;
    font-size: 30px;
    letter-spacing: 3px;
    color: var(--gold);
  }
</style>
</head>
<body>
  <main class="canvas">
    <section class="label" aria-label="Weinetikett Kelvora Rotling 2020">
      <header class="label__head">
        <h1 class="brand-name">Kelvora</h1>
        <p class="tagline">When we gather,<br>good things unfold</p>
      </header>
      <div class="label__variety">
        <span class="variety">ROTLING</span>
        <span class="vintage">2020</span>
      </div>
      <footer class="label__foot">
        <span class="family-name">Dormak</span>
      </footer>
    </section>
  </main>
</body>
</html>
```